Business Card Design for Property Development Company Director

I am looking for a professional and unforgettable business card design for our Director of our Property Development Company.
Please see attached .pptx file to find out what information to include. You don't have to follow the exact format shown in the file - I am interested to see your creative flair using the information provided.

```html
<!DOCTYPE html>
<html lang="en">
<head>
<meta charset="utf-8">
<title>Norvale Property Group – Business Card</title>
<link href="https://fonts.googleapis.com/css2?family=Montserrat:wght@400;500;600;700;800&display=swap" rel="stylesheet">
<style>
  :root {
    --brand-blue: #0d4f9c;
    --brand-blue-soft: #1a5ca8;
    --ink: #3a3a3a;
    --ink-muted: #555;
    --paper: #f6f6f6;
    --tint: #e3e6ea;
    --backdrop: #d9d9d9;
    --white: #ffffff;
  }
  * { box-sizing: border-box; margin: 0; padding: 0; }
  html, body { width: 1200px; height: 1021px; overflow: hidden; }
  body {
    background: var(--backdrop);
    font-family: "Montserrat", sans-serif;
    position: relative;
  }
  .card {
    position: absolute;
    left: 220px;
    width: 760px;
    height: 464px;
    overflow: hidden;
    box-shadow: 0 4px 14px rgba(0,0,0,0.18);
  }
  /* Front */
  .card--front { top: 30px; background: var(--brand-blue); color: var(--white); }
  .front__tagline {
    position: absolute; top: 52px; width: 100%; text-align: center;
    font-size: 19px; font-weight: 400; letter-spacing: 0.5px;
  }
  .front__decor {
    position: absolute; left: 285px; top: 95px; width: 260px; height: 300px;
    background: var(--brand-blue-soft);
  }
  .front__brand {
    position: absolute; top: 190px; width: 100%;
    display: flex; align-items: center; justify-content: center; gap: 18px;
  }
  .brand__mark { width: 54px; height: 54px; background: currentColor; }
  .brand__name { font-size: 40px; font-weight: 700; letter-spacing: 1px; text-transform: uppercase; line-height: 1; }
  .front__cta {
    position: absolute; bottom: 52px; width: 100%; text-align: center;
    font-size: 19px; font-weight: 400; letter-spacing: 0.4px;
  }
  .front__cta strong { font-weight: 800; }
  /* Back */
  .card--back { top: 527px; background: var(--paper); color: var(--ink); }
  .back__decor {
    position: absolute; left: 60px; top: 120px; width: 300px; height: 344px;
    background: var(--tint);
  }
  .back__brand {
    position: absolute; left: 48px; top: 44px;
    display: flex; align-items: center; gap: 14px; color: var(--brand-blue);
  }
  .back__brand .brand__mark { width: 40px; height: 40px; }
  .back__brand .brand__name { font-size: 28px; }
  .contact {
    position: absolute; right: 48px; bottom: 46px; text-align: right;
  }
  .contact__name { font-size: 27px; font-weight: 700; color: var(--brand-blue); }
  .contact__role { font-size: 20px; color: var(--ink-muted); margin-bottom: 22px; }
  .contact__line {
    display: flex; justify-content: flex-end; align-items: center; gap: 10px;
    font-size: 20px; line-height: 1.45; color: var(--ink);
  }
  .contact__line svg { width: 20px; height: 20px; fill: none; stroke: var(--brand-blue); stroke-width: 2; }
  .contact__line--license { padding-right: 30px; }
</style>
</head>
<body>
  <section class="card card--front">
    <div class="front__decor"></div>
    <p class="front__tagline">Property Development &amp; Site Acquisition Specialists</p>
    <div class="front__brand">
      <span class="brand__mark"></span>
      <span class="brand__name">Norvale Property Group</span>
    </div>
    <p class="front__cta">Ask me about our <strong>INVESTMENT &amp; PARTNERSHIP</strong> opportunities</p>
  </section>

  <section class="card card--back">
    <div class="back__decor"></div>
    <div class="back__brand">
      <span class="brand__mark"></span>
      <span class="brand__name">Norvale Property Group</span>
    </div>
    <div class="contact">
      <p class="contact__name">Daniel Marsh</p>
      <p class="contact__role">Director</p>
      <p class="contact__line">0400 318 627
        <svg viewBox="0 0 24 24"><path d="M5 3h4l2 5-3 2a11 11 0 0 0 6 6l2-3 5 2v4a2 2 0 0 1-2 2A17 17 0 0 1 3 5a2 2 0 0 1 2-2z"/></svg>
      </p>
      <p class="contact__line">daniel@norvale.com.au
        <svg viewBox="0 0 24 24"><rect x="3" y="5" width="18" height="14"/><path d="M3 5l9 8 9-8"/></svg>
      </p>
      <p class="contact__line">www.norvale.com.au
        <svg viewBox="0 0 24 24"><circle cx="12" cy="12" r="9"/><path d="M3 12h18M12 3c3 3 3 15 0 18M12 3c-3 3-3 15 0 18"/></svg>
      </p>
      <p class="contact__line contact__line--license">Real Estate Lic: 5192036 &amp; 5192037</p>
    </div>
  </section>
</body>
</html>
```